Business Card for Field Bloom-Eco Friendly Organic Clothing Brand

We are looking for an amazing business card for our eco friendly, organic clothing brand. We are thinking maybe a business card with a peel off sticker on the back, since our hanging clothing tag is a peel off sticker on the back. I will attach our hang tag so we can make sure we stay in line with our design. I've also attached a bag we are doing because I do like the scattered emblem look as well.

```html
<!DOCTYPE html>
<html lang="en">
<head>
<meta charset="UTF-8">
<title>Field Bloom – Business Card</title>
<link href="https://fonts.googleapis.com/css2?family=Montserrat:wght@700;800&family=Open+Sans:wght@400;600;700&display=swap" rel="stylesheet">
<style>
  :root {
    --page: #ecebe8;
    --card-dark: #2d2e2a;
    --card-dark-deep: #1f201d;
    --gold: #d4ad45;
    --gold-light: #f1d98a;
    --gold-deep: #9c7a22;
    --white: #ffffff;
    --ink: #1d1d1d;
    --ink-soft: #3a3a3a;
    --silhouette: #e6e6e6;
  }
  * { box-sizing: border-box; margin: 0; padding: 0; }
  html, body { width: 1200px; height: 900px; overflow: hidden; }
  body { background: var(--page); position: relative; font-family: "Open Sans", sans-serif; }

  .card {
    position: absolute;
    width: 560px;
    height: 320px;
    border-radius: 4px;
    overflow: hidden;
    box-shadow: 0 10px 28px rgba(0,0,0,0.18);
  }

  /* Front side */
  .card-front { left: 110px; top: 130px; background: var(--card-dark); }
  .emblem-pattern {
    position: absolute; inset: 0;
    background:
      radial-gradient(circle at 18% 25%, rgba(212,173,69,0.38), transparent 22%),
      radial-gradient(circle at 82% 22%, rgba(212,173,69,0.32), transparent 20%),
      radial-gradient(circle at 12% 70%, rgba(212,173,69,0.30), transparent 18%),
      radial-gradient(circle at 88% 55%, rgba(212,173,69,0.28), transparent 18%),
      linear-gradient(135deg, var(--card-dark), var(--card-dark-deep));
  }
  .front-brand {
    position: absolute; left: 170px; top: 42px;
    width: 220px; height: 110px;
    background: var(--card-dark);
    display: flex; flex-direction: column; align-items: center; justify-content: center; gap: 10px;
  }
  .brand-mark { display: flex; align-items: center; gap: 10px; }
  .brand-dot { width: 14px; height: 14px; border-radius: 50%; background: var(--white); }
  .brand-name-light {
    font-family: "Open Sans", sans-serif; font-weight: 700;
    font-size: 34px; color: var(--white); letter-spacing: 0.5px;
  }
  .front-url { font-size: 13px; color: var(--white); letter-spacing: 0.3px; }
  .front-banner {
    position: absolute; left: 70px; right: 14px; bottom: 26px; height: 72px;
    border: 3px solid var(--gold);
    background: var(--card-dark);
    display: flex; align-items: center; justify-content: center;
  }
  .banner-name {
    font-family: "Montserrat", sans-serif; font-weight: 800;
    font-size: 42px; color: var(--gold); letter-spacing: 1px;
  }

  /* Back side */
  .card-back { left: 530px; top: 440px; background: var(--white); }
  .meditation-figure {
    position: absolute; left: 20px; top: 40px; width: 210px; height: 280px;
    border-radius: 90px 90px 20px 20px;
    background: linear-gradient(180deg, #efefef, var(--silhouette));
  }
  .back-logo {
    position: absolute; left: 56px; top: 44px;
    width: 210px; height: 62px; border-radius: 12px;
    background: var(--card-dark);
    display: flex; align-items: center; justify-content: center; gap: 10px;
  }
  .logo-square { width: 16px; height: 16px; background: var(--gold); }
  .brand-name-gold {
    font-family: "Open Sans", sans-serif; font-weight: 700;
    font-size: 22px; color: var(--gold);
  }
  .back-url {
    position: absolute; left: 56px; top: 112px; width: 210px;
    text-align: center; font-size: 10px; color: var(--ink-soft);
  }
  .contact-block { position: absolute; left: 320px; top: 66px; }
  .contact-name { font-size: 21px; font-weight: 700; color: var(--ink); }
  .contact-role { font-size: 13px; color: var(--ink-soft); margin-bottom: 22px; }
  .contact-list { list-style: none; display: flex; flex-direction: column; gap: 6px; padding-left: 28px; }
  .contact-item { display: flex; align-items: center; gap: 10px; font-size: 14px; color: var(--ink); }
  .contact-icon { width: 13px; height: 13px; fill: var(--ink); flex: none; }
</style>
</head>
<body>

  <section class="card card-front" aria-label="Business card front">
    <div class="emblem-pattern" role="img" aria-label="Scattered gold emblems: peace signs, hearts and words such as love, peace, om, namaste and live"></div>
    <div class="front-brand">
      <div class="brand-mark">
        <span class="brand-dot"></span>
        <span class="brand-name-light">Field Bloom</span>
      </div>
      <span class="front-url">www.fieldbloomwear.com</span>
    </div>
    <div class="front-banner">
      <span class="banner-name">Field Bloom</span>
    </div>
  </section>

  <section class="card card-back" aria-label="Business card back">
    <div class="meditation-figure" role="img" aria-label="Faint grey silhouette of a person seated in meditation"></div>
    <div class="back-logo">
      <span class="logo-square"></span>
      <span class="brand-name-gold">Field Bloom</span>
    </div>
    <p class="back-url">www.fieldbloomwear.com</p>

    <div class="contact-block">
      <h1 class="contact-name">Daniel Reyes</h1>
      <p class="contact-role">Managing Director</p>
      <ul class="contact-list">
        <li class="contact-item">
          <svg class="contact-icon" viewBox="0 0 16 16" aria-hidden="true"><path d="M3 1l3 3-2 2c1 2 3 4 5 5l2-2 3 3-2 3C6 14 2 10 1 3z"/></svg>
          044-456-7890
        </li>
        <li class="contact-item">
          <svg class="contact-icon" viewBox="0 0 16 16" aria-hidden="true"><path d="M4 1h7v4H4zM1 6h14v8H1zm3 2v2h2V8zm4 0v2h2V8z"/></svg>
          123-456-7890
        </li>
        <li class="contact-item">
          <svg class="contact-icon" viewBox="0 0 16 16" aria-hidden="true"><path d="M4 0h8v16H4zm2 2v10h4V2zm1 11v1h2v-1z"/></svg>
          123-456-7890
        </li>
        <li class="contact-item">
          <svg class="contact-icon" viewBox="0 0 16 16" aria-hidden="true"><path d="M0 3h16v10H0zm1 1v1l7 5 7-5V4z"/></svg>
          info@youremail.com
        </li>
        <li class="contact-item">
          <svg class="contact-icon" viewBox="0 0 16 16" aria-hidden="true"><path d="M6 10l4-4 1 1-4 4zM3 9l3-3 1 1-3 3 2 2 3-3 1 1-3 3c-1 1-2 1-3 0l-1-1c-1-1-1-2 0-3zm10-2l-3 3-1-1 3-3-2-2-3 3-1-1 3-3c1-1 2-1 3 0l1 1c1 1 1 2 0 3z"/></svg>
          www.website.com
        </li>
      </ul>
    </div>
  </section>

</body>
</html>
```